Cosmetic oil label design

We need a label for a cosmetic oganic Argan Oil. The oil is organic imported from Morocco, cold pressed without any preservatives. The lable is for our round 30ml Airless Bottle with clear body Matte Gold Cap, Shiny Gold Collar. We want to communicate that our product is organic natural and works for all beauty needs. We want the emphasis on the words No preservatives, additives or perfumes
We have attached a picture of the bottle and our compnay's logo.

the bottle demensions are Width/Front: 33.0mm
Length/Depth: 33.0mm
Height: 115.0mm
Lable demensions: Lenght 4inch, width 1.75inch.

let us know if you need any other information, cheers!
Updates

Target Market(s)

Our target customer is mainly women 16-70, and also men or anyone looking to have healthy skin and hair using natural products

Industry/Entity Type

Product

Requirements
Must have
• Front side must have:
- attached logo
-words: Authentic Moroccan Argan Oil, No preservatives, additives or perfumes,
L’Huile d’Argan, Produit du Maroc, Imported from Morocco, 30ml

Back side
-Ingredients: 100% Pure Argania Spinosa (Argan Oil)
-Directions: Message into skin, hair or desired area until completely absorbed
-Manufactured for and distributed by Velora Traders
482 W 97th street New York , NY 10027
Nice to have
• Would be nice if we can fit the following information in the back of the label

Rich in vitamin E and essential fatty acids,Argan oil has several benefits. It Hydrates and nourishes skin and hair. Can be used for treating dry skin, split ends softening cuticles. It works for all types of skin.

```html
<!DOCTYPE html>
<html lang="en">
<head>
<meta charset="utf-8">
<title>Nuriya Moroccan Argan Oil Label</title>
<link rel="stylesheet" href="https://fonts.googleapis.com/css2?family=Cinzel:wght@400;500&family=Arimo:wght@400&display=swap">
<style>
  :root {
    --espresso: #2b1d12;
    --bronze: #5a3e22;
    --gold-deep: #b98a42;
    --gold-mid: #d9a24c;
    --gold-light: #f0c46a;
    --ink: #1f140c;
    --cream: #f6e3a6;
    --olive: #8f8c3d;
  }
  html, body {
    margin: 0;
    padding: 0;
    width: 1200px;
    height: 2740px;
    overflow: hidden;
    background: var(--espresso);
  }
  .label {
    position: relative;
    width: 1200px;
    height: 2740px;
    overflow: hidden;
  }
  .label__backdrop {
    position: absolute;
    inset: 0;
    width: 1200px;
    height: 2740px;
  }
  .label__volume {
    position: absolute;
    top: 30px;
    right: 40px;
    margin: 0;
    font-family: "Arimo", Arial, sans-serif;
    font-size: 68px;
    line-height: 1;
    color: var(--cream);
  }
  .brand {
    position: absolute;
    top: 600px;
    left: 0;
    width: 1200px;
    margin: 0;
    text-align: center;
    font-family: "Cinzel", Georgia, serif;
    font-weight: 500;
    font-size: 210px;
    line-height: 1;
    color: var(--olive);
  }
  .product-name {
    position: absolute;
    top: 1330px;
    left: 0;
    width: 1200px;
    margin: 0;
    text-align: center;
    font-family: "Cinzel", Georgia, serif;
    font-weight: 400;
    font-size: 164px;
    line-height: 220px;
    color: var(--ink);
  }
  .claim {
    position: absolute;
    top: 2280px;
    left: 0;
    width: 1200px;
    margin: 0;
    text-align: center;
    font-family: "Arimo", Arial, sans-serif;
    font-size: 114px;
    line-height: 114px;
    color: var(--cream);
  }
  .origin {
    position: absolute;
    top: 2636px;
    left: 0;
    width: 1200px;
    margin: 0;
    text-align: center;
    font-family: "Arimo", Arial, sans-serif;
    font-size: 70px;
    line-height: 1;
    color: var(--cream);
  }
</style>
</head>
<body>
  <main class="label">
    <svg class="label__backdrop" viewBox="0 0 1200 2740" aria-hidden="true">
      <defs>
        <linearGradient id="goldBody" x1="0" y1="0" x2="0" y2="1">
          <stop offset="0" stop-color="var(--espresso)"/>
          <stop offset="0.32" stop-color="var(--bronze)"/>
          <stop offset="0.4" stop-color="var(--gold-deep)"/>
          <stop offset="0.47" stop-color="var(--gold-mid)"/>
          <stop offset="0.58" stop-color="var(--gold-light)"/>
          <stop offset="1" stop-color="var(--gold-light)"/>
        </linearGradient>
      </defs>
      <rect class="band-body" x="0" y="0" width="1200" height="2740" fill="url(#goldBody)"/>
      <path class="band-top" d="M0,0 H1200 V850 Q600,990 0,850 Z" fill="var(--espresso)"/>
      <path class="band-bottom" d="M0,2230 Q600,2110 1200,2230 V2740 H0 Z" fill="var(--espresso)"/>
    </svg>

    <p class="label__volume">30ml</p>

    <h1 class="brand">Nuriya</h1>

    <h2 class="product-name">MOROCCAN<br>ARGAN<br>OIL</h2>

    <p class="claim">No preservatives,<br>additives or<br>parfumes</p>

    <p class="origin">L’Huile d’Argan, Produit du Maroc.</p>
  </main>
</body>
</html>
```